MintVela business cards

We want to create two sets of cards. One general card for mintvela [staff] and one card for the founder of the company. Below is the general/basic information for you to format/display on side of the cards:
--Company address: 418 Larkmoor Street, New York, NY 10087
--Main phone: 212-736-5182
Will also provide you with secondary 1-800 number
--company website: www.mintvela.example
--email address for general card: frontdesk@mintvela.example
--email address (for dr hollings's card: md@mintvela.example
--titles for dr hollings's card: Founder, Medical Director
--Dr. Hollings's name on the card should read: Gregor T. Hollings, MD
You can also play around with mintvela's tag line: Quiet Glow Keeps Its Promise (TM or R should be attached as a trademark has been filed)
Reason: More time to design something awesome. This company is an aesthetic medical company that offers cool and safe cosmetic treatments
For the business card design for the doctor, please change the doctor's name to look like this above his title: Gregor T. Hollings, MD instead of using Dr. Gregor....etc
Reason: WILL NOT BE ABLE TO VIEW AND FINALIZE DESIGNS UNTIL I RETURN FROM MEDICAL CONFERENCE, WHICH WILL BE ON SUNDAY/MONDAY. MY APOLOGIES
can everyone try making it very minimalistic
A Bit of a change...
Can everyone take a stab at using a grey "raw" or eco friendly stock paper. We are interested to see the designs you come up with.
Business

```html
<!DOCTYPE html>
<html lang="en">
<head>
<meta charset="utf-8">
<title>MintVela Business Card</title>
<link rel="stylesheet" href="https://fonts.googleapis.com/css2?family=Roboto+Condensed:wght@400;700&display=swap">
<style>
:root{
  --page:#e9eaec;
  --card:#ffffff;
  --blue:#3b82c9;
  --blue-deep:#2a6db3;
  --grey:#a9adb3;
  --grey-light:#dfe1e4;
  --ink:#4a4f56;
}
*{margin:0;padding:0;box-sizing:border-box}
html,body{width:1200px;height:681px;overflow:hidden;background:var(--page)}
.card{
  position:absolute;left:110px;top:70px;width:980px;height:541px;
  background:var(--card);overflow:hidden;
  box-shadow:0 10px 30px rgba(0,0,0,.18);
  font-family:"Roboto Condensed",sans-serif;color:var(--ink);
}
.edge-band{position:absolute;left:0;top:0;width:34px;height:100%;background:var(--blue)}
.side-strip{position:absolute;right:0;top:0;width:96px;height:100%;background:var(--grey-light)}
.side-strip::after{content:"";position:absolute;right:0;top:0;width:30px;height:100%;background:var(--blue)}
.side-title{
  position:absolute;right:48px;top:50%;transform:translate(50%,-50%) rotate(90deg);
  white-space:nowrap;font-size:17px;letter-spacing:3px;text-transform:uppercase;color:var(--ink);
}
.brand{position:absolute;left:90px;top:80px}
.brand-name{
  font-weight:700;font-size:84px;line-height:1;
  color:var(--ink);display:flex;align-items:center;gap:18px;
}
.brand-square{width:20px;height:20px;background:var(--blue)}
.tagline{margin-top:14px;font-size:17px;letter-spacing:4px;text-transform:uppercase;color:var(--grey)}
.tagline sup{font-size:10px}
.name-bar{
  position:absolute;left:34px;top:250px;width:850px;height:62px;
  background:linear-gradient(90deg,var(--blue-deep),var(--blue));
  display:flex;align-items:center;
}
.name-icon{width:62px;height:62px;background:var(--card);display:flex;align-items:center;justify-content:center;margin-left:56px}
.person-name{margin-left:24px;color:#fff;font-weight:700;font-size:34px;letter-spacing:3px;text-transform:uppercase;white-space:nowrap}
.contacts{position:absolute;left:152px;top:340px;list-style:none}
.contacts li{display:flex;align-items:center;gap:16px;font-size:20px;height:36px;letter-spacing:.5px}
.contacts svg{width:20px;height:20px;fill:var(--blue);flex:none}
</style>
</head>
<body>
<div class="card">
  <div class="edge-band"></div>
  <div class="side-strip"></div>
  <div class="side-title">Founder, Medical Director</div>

  <div class="brand">
    <div class="brand-name">MintVela<span class="brand-square"></span></div>
    <div class="tagline">Quiet Glow Keeps Its Promise<sup>™</sup></div>
  </div>

  <div class="name-bar">
    <div class="name-icon">
      <svg width="28" height="28" viewBox="0 0 24 24"><circle cx="12" cy="8" r="4.5" fill="#3b82c9"/><path d="M3 22c0-5 4-8 9-8s9 3 9 8z" fill="#3b82c9"/></svg>
    </div>
    <div class="person-name">Gregor T. Hollings, MD</div>
  </div>

  <ul class="contacts">
    <li><svg viewBox="0 0 24 24"><path d="M6.6 10.8a15 15 0 0 0 6.6 6.6l2.2-2.2c.3-.3.7-.4 1-.2 1.1.4 2.3.6 3.6.6.6 0 1 .4 1 1V20c0 .6-.4 1-1 1A17 17 0 0 1 3 4c0-.6.4-1 1-1h3.5c.6 0 1 .4 1 1 0 1.3.2 2.5.6 3.6.1.3 0 .7-.2 1z"/></svg>212-555-0182</li>
    <li><svg viewBox="0 0 24 24"><path d="M6.6 10.8a15 15 0 0 0 6.6 6.6l2.2-2.2c.3-.3.7-.4 1-.2 1.1.4 2.3.6 3.6.6.6 0 1 .4 1 1V20c0 .6-.4 1-1 1A17 17 0 0 1 3 4c0-.6.4-1 1-1h3.5c.6 0 1 .4 1 1 0 1.3.2 2.5.6 3.6.1.3 0 .7-.2 1z"/></svg>1-800-555-0148</li>
    <li><svg viewBox="0 0 24 24"><path d="M2 5h20v14H2z M3 6l9 7 9-7" fill="none" stroke="#3b82c9" stroke-width="2"/></svg>md@mintvela.example</li>
    <li><svg viewBox="0 0 24 24"><circle cx="12" cy="12" r="9" fill="none" stroke="#3b82c9" stroke-width="2"/><path d="M3 12h18M12 3c3 3 3 15 0 18M12 3c-3 3-3 15 0 18" fill="none" stroke="#3b82c9" stroke-width="1.5"/></svg>www.mintvela.example</li>
    <li><svg viewBox="0 0 24 24"><path d="M12 2a7 7 0 0 0-7 7c0 5 7 13 7 13s7-8 7-13a7 7 0 0 0-7-7zm0 9.5A2.5 2.5 0 1 1 12 6.5a2.5 2.5 0 0 1 0 5z"/></svg>418 Larkmoor Street, New York, NY 10087</li>
  </ul>
</div>
</body>
</html>
```